Website for Apartment Rental in Prague

I would like to create designs of my website focused on luxury apartment rentals in Prague, Czech Republic. I created initial mock-ups, They are all attached. I need to design homepage and subpage. The mock-ups were created by combining elements from different websites that I liked but I need you to create a design that is unique and original. The attached files a only a guidance for the structure of the website but not for the design. Try to be creative.

Apartment

```html
<!DOCTYPE html>
<html lang="en">
<head>
<meta charset="utf-8">
<title>Vltava Suites – Apartment Rentals</title>
<link href="https://fonts.googleapis.com/css2?family=Open+Sans:ital,wght@0,400;0,600;0,700;1,400&display=swap" rel="stylesheet">
<style>
:root{
  --gold:#bfae80;
  --gold-dark:#a8966a;
  --gold-soft:#d9cfb2;
  --ink:#222222;
  --muted:#666666;
  --line:#d6d0c0;
  --white:#ffffff;
  --dark:#2e2e2e;
  --darker:#1f1f1f;
  --slate:#3b3e42;
}
*{box-sizing:border-box;margin:0;padding:0}
html,body{width:1200px;height:3982px;overflow:hidden}
body{font-family:"Open Sans",Arial,sans-serif;color:var(--ink);background:var(--white);position:relative}
.abs{position:absolute}
.photo{position:absolute;display:block}

/* hero */
.hero{position:absolute;left:0;top:0;width:1200px;height:563px;background:linear-gradient(160deg,#6f655a 0%,#8c7f70 35%,#4a4540 70%,#2e2b28 100%)}
.brand{position:absolute;left:80px;top:30px;color:var(--white)}
.brand small{display:block;font-size:14px;letter-spacing:5px;font-weight:400;opacity:.85}
.brand strong{display:block;font-size:34px;letter-spacing:6px;font-weight:600;line-height:1}
.nav{position:absolute;right:80px;top:38px;display:flex;gap:24px;font-size:17px;font-weight:600;color:var(--white)}
.nav .active{color:var(--gold)}
.booking{position:absolute;left:111px;top:252px;width:972px;height:160px;background:rgba(40,36,32,.55)}
.field{position:absolute;height:44px;background:var(--white);border:1px solid #ddd;font-size:14px;font-style:italic;color:#999;padding:12px 14px}
.field.select::after{content:"";position:absolute;right:0;top:0;width:36px;height:42px;border-left:1px solid #ddd;background:#f2f2f2}
.field.select::before{content:"";position:absolute;right:13px;top:16px;width:8px;height:8px;border-right:2px solid #888;border-bottom:2px solid #888;transform:rotate(45deg);z-index:1}
.btn-gold{position:absolute;background:var(--gold);color:var(--white);font-weight:600;font-size:16px;text-align:center;text-transform:uppercase}
.or{position:absolute;color:var(--white);font-size:15px}

/* offer band */
.offer{position:absolute;left:0;top:563px;width:1200px;height:106px;background:var(--gold)}
.offer h2{position:absolute;left:80px;top:32px;color:var(--white);font-size:30px;font-weight:600}
.btn-dark{position:absolute;left:958px;top:37px;width:165px;height:43px;background:var(--darker);color:var(--white);font-size:18px;font-weight:600;text-align:center;line-height:43px}

/* intro tiles */
.tile{position:absolute;top:741px;width:496px;height:342px}
.tile .frame{position:absolute;left:18px;top:18px;right:18px;bottom:18px;border:2px solid rgba(255,255,255,.85)}
.tile-travel{left:80px;background:linear-gradient(135deg,#c8c6c2,#8d8a85 55%,#5a5753)}
.tile-travel .caption{position:absolute;left:28px;bottom:24px;color:var(--white);font-size:24px;font-weight:600}
.tile-interiors{left:624px;background:linear-gradient(135deg,#d0c29c,#b3a27a 60%,#9b8b63)}
.tile-interiors h3{position:absolute;left:0;right:0;top:80px;text-align:center;color:var(--ink);font-size:28px;font-weight:400}
.tile-interiors h3 em{font-style:italic}
.tile-interiors p{position:absolute;left:60px;right:60px;top:128px;text-align:center;color:var(--white);font-size:14px;line-height:1.5}
.btn-outline-dark{position:absolute;left:172px;top:212px;width:152px;height:40px;border:2px solid var(--ink);color:var(--ink);font-size:16px;font-weight:600;text-align:center;line-height:36px}

.section-title{position:absolute;left:0;width:1200px;text-align:center;font-size:42px;font-weight:400;color:var(--ink)}

/* rental cards */
.rental{position:absolute;top:1213px;width:321px;height:367px;border:1px solid var(--line);background:var(--white)}
.rental .photo{left:0;top:0;width:319px;height:208px}
.badge{position:absolute;left:0;top:14px;background:var(--gold);color:var(--white);font-size:13px;padding:5px 12px}
.heart{position:absolute;left:12px;top:178px}
.rental h4{position:absolute;left:12px;top:226px;font-size:18px;font-weight:600}
.meta{position:absolute;font-size:15px;color:var(--muted)}
.meta span+span{margin-left:26px}
.rental .meta{left:12px;top:262px}
.card-btn{position:absolute;height:40px;font-size:14px;text-align:center;line-height:38px;text-transform:uppercase}
.card-btn.solid{background:var(--gold);color:var(--white);border:1px solid var(--gold)}
.card-btn.ghost{border:1px solid var(--gold);color:var(--gold-dark);background:var(--white)}
.rental .solid{left:12px;top:302px;width:136px}
.rental .ghost{left:168px;top:302px;width:136px}
.pager{position:absolute;top:1608px;width:30px;height:30px;background:var(--gold)}

/* need to know */
.know{position:absolute;left:0;top:1691px;width:1200px;height:499px;background:var(--gold)}
.know h2{position:absolute;left:0;right:0;top:36px;text-align:center;color:var(--white);font-size:40px;font-weight:400}
.know svg{position:absolute;left:0;top:0}
.know-item{position:absolute;top:360px;width:360px;text-align:center;color:var(--white)}
.know-item h4{font-size:22px;font-weight:400}
.know-item p{font-size:14px;line-height:1.5;margin-top:6px;opacity:.95}

/* featured */
.deal{position:absolute;width:242px;height:284px}
.deal .photo{left:0;top:0;width:242px;height:167px}
.ribbon{position:absolute;left:0;top:0;width:0;height:0;border-top:70px solid #2a2a2a;border-right:70px solid transparent}
.ribbon-text{position:absolute;left:2px;top:20px;color:var(--white);font-size:12px;transform:rotate(-45deg)}
.deal h4{position:absolute;left:0;top:180px;font-size:19px;font-weight:400}
.deal .meta{left:0;top:214px;font-size:15px}
.deal .solid{left:0;top:244px;width:110px;height:36px;line-height:34px;font-size:14px;color:var(--ink);text-transform:none}
.deal .ghost{left:124px;top:244px;width:110px;height:36px;line-height:34px;font-size:13px;color:#9a8a60}

/* testimonial */
.quote{position:absolute;left:0;top:2992px;width:1200px;height:260px;background:linear-gradient(90deg,#3a3d41,#2f3236 50%,#3a3d41)}
.quote p{position:absolute;left:180px;right:180px;top:110px;text-align:center;color:var(--white);font-size:15px;font-style:italic;line-height:1.7}
.quote .who{position:absolute;left:0;right:0;top:175px;text-align:center;color:var(--white);font-size:20px}

/* news */
.news{position:absolute;top:3361px;width:332px}
.news .photo{position:relative;width:332px;height:205px}
.news h4{margin-top:16px;font-size:18px;font-weight:600;line-height:1.45}
.news .date{margin-top:10px;font-size:14px;color:var(--ink);display:flex;align-items:center;gap:8px}
.news p{margin-top:8px;font-size:14px;color:var(--muted);line-height:1.6}
.news p b{color:var(--gold);font-weight:700}

/* footer */
.footer{position:absolute;left:0;top:3762px;width:1200px;height:168px;background:var(--dark)}
.foot-col{position:absolute;top:50px;height:90px;color:var(--white)}
.foot-col h5{font-size:20px;font-weight:400;color:var(--gold)}
.foot-col p{font-size:14px;margin-top:10px;line-height:1.6}
.divider{position:absolute;top:42px;width:1px;height:100px;background:#555}
.social{display:flex;gap:16px;margin-top:16px}
.social span{width:18px;height:18px;border-radius:50%;background:#cfcfcf;display:block}
.copyright{position:absolute;left:0;top:3930px;width:1200px;height:52px;background:var(--darker);color:var(--white);font-size:14px;text-align:center;line-height:52px}
</style>
</head>
<body>

<header class="hero">
  <div class="photo" role="img" aria-label="Bright modern living room with dark sofa, floor lamp and dining area by tall windows" style="inset:0;background:linear-gradient(160deg,rgba(120,110,98,.3),rgba(40,36,32,.35))"></div>
  <div class="brand"><small>VLTAVA</small><strong>SUITES</strong></div>
  <nav class="nav">
    <span class="active">Apartment</span><span>Location</span><span>Services</span><span>Gallery</span><span>News</span><span>Offers&amp;Tours</span><span>For Families</span><span>Contact</span>
  </nav>
  <form class="booking">
    <div class="field" style="left:38px;top:29px;width:204px">Check in date</div>
    <div class="field" style="left:255px;top:29px;width:197px">Check out date</div>
    <div class="field select" style="left:473px;top:29px;width:146px">Adults</div>
    <div class="field select" style="left:640px;top:29px;width:144px">Childrens</div>
    <div class="field select" style="left:807px;top:29px;width:133px">Infants</div>
    <div class="field" style="left:38px;top:93px;width:374px">Promotion code</div>
    <div class="btn-gold" style="left:430px;top:93px;width:221px;height:44px;line-height:44px">Check Availability</div>
    <span class="or" style="left:676px;top:104px">OR</span>
    <div class="field select" style="left:715px;top:93px;width:225px">Select Rental Unit</div>
  </form>
</header>

<section class="offer">
  <h2>Official Site - Best Price Guaranteed</h2>
  <div class="btn-dark">BOOK NOW</div>
</section>

<section>
  <div class="tile tile-travel" role="img" aria-label="Open-plan apartment interior with city view windows">
    <div class="frame"></div>
    <div class="caption">Different Vision of Travelling</div>
  </div>
  <div class="tile tile-interiors" role="img" aria-label="Warm-toned designer interior behind a gold overlay">
    <div class="frame"></div>
    <h3>Interiors Designed by <em>Maison Lumen</em></h3>
    <p>Maison Lumen Apartments offers short term as well as long term options in our studio apartments and our one bedroom apartment homes.</p>
    <div class="btn-outline-dark">LEARN MORE</div>
  </div>
</section>

<h2 class="section-title" style="top:1140px">Rental Apartments</h2>

<section>
  <article class="rental" style="left:80px">
    <div class="photo" role="img" aria-label="Modern apartment building at dusk" style="background:linear-gradient(180deg,#3a4a8c,#6b7bb0 55%,#c9c3b8)"></div>
    <span class="badge">From&nbsp; 150 USD</span>
    <svg class="heart" width="20" height="18" viewBox="0 0 20 18"><path d="M10 17 2 9a4.5 4.5 0 0 1 8-5 4.5 4.5 0 0 1 8 5z" fill="#fff"/></svg>
    <h4>Lorem Ipsum is simply dummy.</h4>
    <div class="meta"><span>1 Bedroom</span><span>4 max People</span></div>
    <div class="card-btn solid">Book Now</div><div class="card-btn ghost">Details</div>
  </article>
  <article class="rental" style="left:441px">
    <div class="photo" role="img" aria-label="Residential apartment tower with balconies" style="background:linear-gradient(180deg,#dfe6ee,#b99a7c 55%,#8a7f74)"></div>
    <span class="badge">From&nbsp; 150 USD</span>
    <svg class="heart" width="20" height="18" viewBox="0 0 20 18"><path d="M10 17 2 9a4.5 4.5 0 0 1 8-5 4.5 4.5 0 0 1 8 5z" fill="#fff"/></svg>
    <h4>Lorem Ipsum is simply dummy.</h4>
    <div class="meta"><span>1 Bedroom</span><span>4 Max People</span></div>
    <div class="card-btn solid">Book Now</div><div class="card-btn ghost">Details</div>
  </article>
  <article class="rental" style="left:802px">
    <div class="photo" role="img" aria-label="Glass-walled lobby with columns" style="background:linear-gradient(180deg,#e8e4de,#b9b2a8 55%,#8f877c)"></div>
    <span class="badge">From&nbsp; 150 USD</span>
    <svg class="heart" width="20" height="18" viewBox="0 0 20 18"><path d="M10 17 2 9a4.5 4.5 0 0 1 8-5 4.5 4.5 0 0 1 8 5z" fill="#fff"/></svg>
    <h4>Lorem Ipsum is simply dummy.</h4>
    <div class="meta"><span>1 Bedroom</span><span>4 max People</span></div>
    <div class="card-btn solid">Book Now</div><div class="card-btn ghost">Details</div>
  </article>
  <svg class="pager" style="left:80px" viewBox="0 0 30 30"><rect width="30" height="30" fill="#bfae80"/><path d="M18 9 12 15l6 6" stroke="#fff" stroke-width="2" fill="none"/></svg>
  <svg class="pager" style="left:1093px" viewBox="0 0 30 30"><rect width="30" height="30" fill="#bfae80"/><path d="M12 9l6 6-6 6" stroke="#fff" stroke-width="2" fill="none"/></svg>
</section>

<section class="know">
  <h2>Need To Know</h2>
  <svg width="1200" height="499" viewBox="0 0 1200 499">
    <path d="M0 230 C120 150 180 150 231 189 C340 260 480 270 595 268 C720 266 860 250 982 189 C1060 150 1130 170 1200 230" stroke="rgba(255,255,255,.55)" stroke-width="2" fill="none"/>
    <g fill="none" stroke="#fff" stroke-width="2">
      <rect x="20" y="232" width="16" height="22"/><rect x="1144" y="232" width="16" height="22"/>
    </g>
    <circle cx="231" cy="189" r="72" fill="#fff" opacity=".35"/><circle cx="231" cy="189" r="58" fill="#fff"/><circle cx="231" cy="189" r="46" fill="#bfae80"/>
    <g fill="none" stroke="#fff" stroke-width="3"><rect x="214" y="168" width="34" height="42"/><path d="M222 178h6M234 178h6M222 188h6M234 188h6M222 198h6M234 198h6"/></g>
    <circle cx="595" cy="268" r="72" fill="#fff" opacity=".35"/><circle cx="595" cy="268" r="58" fill="#fff"/><circle cx="595" cy="268" r="46" fill="#bfae80"/>
    <g fill="none" stroke="#fff" stroke-width="3"><path d="M588 248h-14v40h14"/><path d="M584 268h30M606 260l8 8-8 8"/></g>
    <circle cx="982" cy="189" r="72" fill="#fff" opacity=".35"/><circle cx="982" cy="189" r="58" fill="#fff"/><circle cx="982" cy="189" r="46" fill="#bfae80"/>
    <g fill="none" stroke="#fff" stroke-width="3"><path d="M956 188l26-24 26 24M963 182v28h38v-28"/><circle cx="990" cy="198" r="9"/></g>
    <text x="990" y="203" fill="#fff" font-size="13" font-family="Open Sans,sans-serif" text-anchor="middle">$</text>
  </svg>
  <div class="know-item" style="left:51px"><h4>Apartments</h4><p>also available to rent all the apartments<br>together for companies or larger group</p></div>
  <div class="know-item" style="left:415px"><h4>Check-Out</h4><p>12 noon; earliest check-in 3pm both are<br>flexible, by arrangement</p></div>
  <div class="know-item" style="left:802px"><h4>Rates</h4><p>Prices from 150 USD per night, including<br>tax</p></div>
</section>

<h2 class="section-title" style="top:2220px">Featured Deals</h2>

<section>
  <!-- row 1 -->
  <article class="deal" style="left:80px;top:2297px"><div class="photo" role="img" aria-label="Living room with grey sofa and yellow accents" style="background:linear-gradient(135deg,#d6d2ca,#6a6863 55%,#c9a43a)"></div><div class="ribbon"></div><span class="ribbon-text">Featured</span><h4>Apartment</h4><div class="meta"><span>1 Bedroom</span><span>4 max People</span></div><div class="card-btn solid">152 USD</div><div class="card-btn ghost">VIEW DETAIL</div></article>
  <article class="deal" style="left:346px;top:2297px"><div class="photo" role="img" aria-label="Bright lounge with large windows" style="background:linear-gradient(135deg,#e8e6e0,#a9a49a 55%,#4e4b46)"></div><div class="ribbon"></div><span class="ribbon-text">Featured</span><h4>Apartment</h4><div class="meta"><span>1 Bedroom</span><span>4 max People</span></div><div class="card-btn solid">152 USD</div><div class="card-btn ghost">VIEW DETAIL</div></article>
  <article class="deal" style="left:612px;top:2297px"><div class="photo" role="img" aria-label="Warm wooden-floored apartment interior" style="background:linear-gradient(135deg,#e2d8c8,#b38a62 55%,#6e5640)"></div><div class="ribbon"></div><span class="ribbon-text">Featured</span><h4>Apartment</h4><div class="meta"><span>1 Bedroom</span><span>4 max People</span></div><div class="card-btn solid">152 USD</div><div class="card-btn ghost">VIEW DETAIL</div></article>
  <article class="deal" style="left:878px;top:2297px"><div class="photo" role="img" aria-label="Light apartment with glass balcony doors" style="background:linear-gradient(135deg,#f0eee9,#c6c2b8 55%,#8c8880)"></div><div class="ribbon"></div><span class="ribbon-text">Featured</span><h4>Apartment</h4><div class="meta"><span>1 Bedroom</span><span>4 max People</span></div><div class="card-btn solid">152 USD</div><div class="card-btn ghost">VIEW DETAIL</div></article>
  <!-- row 2 -->
  <article class="deal" style="left:80px;top:2628px"><div class="photo" role="img" aria-label="Living room with grey sofa and yellow accents" style="background:linear-gradient(135deg,#d6d2ca,#6a6863 55%,#c9a43a)"></div><div class="ribbon"></div><span class="ribbon-text">Featured</span><h4>Apartment</h4><div class="meta"><span>1 Bedroom</span><span>4 max People</span></div><div class="card-btn solid">152 USD</div><div class="card-btn ghost">VIEW DETAIL</div></article>
  <article class="deal" style="left:346px;top:2628px"><div class="photo" role="img" aria-label="Bright lounge with large windows" style="background:linear-gradient(135deg,#e8e6e0,#a9a49a 55%,#4e4b46)"></div><div class="ribbon"></div><span class="ribbon-text">Featured</span><h4>Apartment</h4><div class="meta"><span>1 Bedroom</span><span>4 max People</span></div><div class="card-btn solid">152 USD</div><div class="card-btn ghost">VIEW DETAIL</div></article>
  <article class="deal" style="left:612px;top:2628px"><div class="photo" role="img" aria-label="Warm wooden-floored apartment interior" style="background:linear-gradient(135deg,#e2d8c8,#b38a62 55%,#6e5640)"></div><div class="ribbon"></div><span class="ribbon-text">Featured</span><h4>Apartment</h4><div class="meta"><span>1 Bedroom</span><span>4 max People</span></div><div class="card-btn solid">152 USD</div><div class="card-btn ghost">VIEW DETAIL</div></article>
  <article class="deal" style="left:878px;top:2628px"><div class="photo" role="img" aria-label="Light apartment with glass balcony doors" style="background:linear-gradient(135deg,#f0eee9,#c6c2b8 55%,#8c8880)"></div><div class="ribbon"></div><span class="ribbon-text">Featured</span><h4>Apartment</h4><div class="meta"><span>1 Bedroom</span><span>4 max People</span></div><div class="card-btn solid">152 USD</div><div class="card-btn ghost">VIEW DETAIL</div></article>
</section>

<section class="quote" role="img" aria-label="Dim city skyline behind a testimonial">
  <svg class="abs" style="left:0;top:0" width="1200" height="260" viewBox="0 0 1200 260">
    <path d="M150 61H548M652 61H1050" stroke="#8a8a80" stroke-width="1"/>
    <g fill="#bfae80"><path d="M572 48h20v14c0 10-6 18-16 20l-2-5c6-2 8-6 8-10h-10z"/><path d="M604 48h20v14c0 10-6 18-16 20l-2-5c6-2 8-6 8-10h-10z"/></g>
    <g fill="none" stroke="#fff" stroke-width="1.5"><circle cx="566" cy="223" r="6"/><circle cx="584" cy="223" r="6"/><circle cx="602" cy="223" r="6"/></g>
    <circle cx="620" cy="223" r="7" fill="#bfae80"/>
  </svg>
  <p>"Lorem Ipsum is simply dummy text of the printing and typesetting industry. Lorem Ipsum has been the industry's standard dummy text ever since the 1500s, when an unknown printer took a galley of type and scrambled."</p>
  <div class="who">- Client Name</div>
</section>

<h2 class="section-title" style="top:3285px">Latest News</h2>

<section>
  <article class="news" style="left:80px"><div class="photo" role="img" aria-label="Hand handing over apartment keys" style="background:linear-gradient(135deg,#f2efe9,#d8c3ae 50%,#8a3a2a)"></div><h4>Lorem Ipsum is simply dummy text of the printing</h4><div class="date"><svg width="14" height="14" viewBox="0 0 14 14"><rect x="1" y="2" width="12" height="11" fill="none" stroke="#333" stroke-width="1.5"/><path d="M1 5h12" stroke="#333" stroke-width="1.5"/></svg>12th April 2016</div><p>Lorem Ipsum is simply dummy text of the printing and typesetting industry... <b>»</b></p></article>
  <article class="news" style="left:435px"><div class="photo" role="img" aria-label="Sunlit living room with sofa and wall art" style="background:linear-gradient(135deg,#e9e4dc,#c4b8a6 55%,#7d6f5e)"></div><h4>Lorem Ipsum is simply dummy text of the printing</h4><div class="date"><svg width="14" height="14" viewBox="0 0 14 14"><rect x="1" y="2" width="12" height="11" fill="none" stroke="#333" stroke-width="1.5"/><path d="M1 5h12" stroke="#333" stroke-width="1.5"/></svg>12th April 2016</div><p>Lorem Ipsum is simply dummy text of the printing and typesetting industry... <b>»</b></p></article>
  <article class="news" style="left:789px"><div class="photo" role="img" aria-label="Dining area with staircase and leather chairs" style="background:linear-gradient(135deg,#ece8e2,#a88b6a 55%,#4e3e30)"></div><h4>Lorem Ipsum is simply dummy text of the printing</h4><div class="date"><svg width="14" height="14" viewBox="0 0 14 14"><rect x="1" y="2" width="12" height="11" fill="none" stroke="#333" stroke-width="1.5"/><path d="M1 5h12" stroke="#333" stroke-width="1.5"/></svg>12th April 2016</div><p>Lorem Ipsum is simply dummy text of the printing and typesetting industry... <b>»</b></p></article>
</section>

<footer class="footer">
  <div class="foot-col" style="left:80px"><h5>Telephone</h5><p>555 010 2040</p></div>
  <div class="divider" style="left:330px"></div>
  <div class="foot-col" style="left:350px"><h5>Email Us</h5><p>info@vltavasuites.com</p></div>
  <div class="divider" style="left:600px"></div>
  <div class="foot-col" style="left:621px;width:240px"><h5>Address</h5><p>Lorem Ipsum is simply dummy text of the printing.</p></div>
  <div class="divider" style="left:866px"></div>
  <div class="foot-col" style="left:884px"><h5>Follow Us</h5><div class="social"><span></span><span></span><span></span><span></span></div></div>
</footer>
<div class="copyright">2017 ©VLTAVA SUITES. - All Rights Reserved.</div>

</body>
</html>
```